Casino with the 'highest winning percentage' needs a stationery design

This is for a casino in Colombo, Sri Lanka and we need a stationery design for business card, letter head and envelope.

Should be very professional, simple and elegant without fancy fonts

Reason: Not fully satisfied with the designs. Need more designs.

Business

• 1. card deck symbol 'CLUBS' in red, or black

2. name in BLOCK CAPITAL LETTERS

3. Preferred font colours are black, white or red

4. Prefer 'professional /elegant' fonts
• SHOULD NOT HAVE ANY OTHER SYMBOL EXCEPT 'CLUBS'

DO NOT PREFER ITALIC FONTS

```html
<!DOCTYPE html>
<html lang="en">
<head>
<meta charset="utf-8">
<title>Corvane Entertainment – Business Card</title>
<link href="https://fonts.googleapis.com/css2?family=Caladea:wght@400;700&display=swap" rel="stylesheet">
<style>
  :root {
    --page-bg: #d8d3cc;
    --metal-light: #f1f1f1;
    --metal-mid: #c9c9c9;
    --metal-dark: #9c9c9c;
    --card-edge: #5a5a5a;
    --brand-red: #d42b3c;
    --ink: #231f20;
    --white: #ffffff;
  }
  * { box-sizing: border-box; margin: 0; padding: 0; }
  html, body {
    width: 1193px; height: 1200px; overflow: hidden;
    background: var(--page-bg);
    font-family: "Caladea", "Cambria", Georgia, serif;
  }
  .stage { position: relative; width: 1193px; height: 1200px; }

  .card {
    position: absolute;
    width: 914px; height: 523px;
    border-radius: 44px;
    border: 1px solid var(--card-edge);
    overflow: hidden;
    background:
      repeating-linear-gradient(90deg, rgba(255,255,255,0.10) 0 2px, rgba(0,0,0,0.04) 2px 5px, rgba(255,255,255,0.06) 5px 9px),
      linear-gradient(180deg, var(--metal-light) 0%, var(--metal-mid) 45%, var(--metal-dark) 75%, var(--metal-mid) 100%);
  }
  .card--front { left: 61px; top: 57px; }
  .card--back { left: 218px; top: 623px; }

  .brand-dot {
    position: absolute;
    border-radius: 50%;
    background: var(--brand-red);
  }
  .card--front .brand-dot { left: 84px; top: 48px; width: 140px; height: 140px; }
  .card--back .brand-dot { left: 113px; top: 150px; width: 165px; height: 165px; }

  .brand-name {
    position: absolute;
    color: var(--ink);
    font-weight: 700;
    text-transform: uppercase;
    letter-spacing: 0.5px;
  }
  .card--front .brand-name { left: 270px; top: 52px; font-size: 52px; line-height: 64px; }
  .card--back .brand-name { left: 322px; top: 160px; font-size: 58px; line-height: 72px; }

  .footer-band {
    position: absolute; left: 0; right: 0; top: 424px; bottom: 0;
    background: var(--brand-red);
  }

  .contact-list {
    position: absolute; left: 93px; top: 233px;
    list-style: none; color: var(--white);
    font-size: 25px; line-height: 37px;
  }
  .contact-list li { display: flex; align-items: center; gap: 12px; }
  .contact-icon { width: 21px; height: 21px; flex: none; }

  .company-address {
    position: absolute; right: 36px; top: 428px;
    text-align: right; color: var(--white);
    font-size: 24px; line-height: 30px; font-style: normal;
  }
  .company-address strong { display: block; font-weight: 700; }

  .tagline {
    position: absolute; left: 0; right: 0; top: 364px;
    text-align: center; color: var(--brand-red);
    font-size: 29px; font-weight: 700; letter-spacing: 5.4px;
  }
  .web-address {
    position: absolute; left: 0; right: 0; top: 460px;
    text-align: center; color: var(--ink);
    font-size: 27px; letter-spacing: 8.5px;
  }
</style>
</head>
<body>
<main class="stage">

  <section class="card card--front" aria-label="Business card front">
    <div class="footer-band" role="img" aria-label="Red footer band"></div>

    <div class="brand-dot" aria-hidden="true"></div>
    <h1 class="brand-name">Corvane<br>Entertainment</h1>

    <ul class="contact-list">
      <li>
        <svg class="contact-icon" viewBox="0 0 24 24" aria-hidden="true"><circle cx="12" cy="12" r="10.5" fill="none" stroke="#fff" stroke-width="1.6"/><path d="M8.5 7 l2 2.2 -1.2 1.4 c.8 1.7 2 2.9 3.6 3.7 l1.4 -1.2 2.2 2 -1.6 1.7 C11 16.2 7.6 12.8 7 8.6z" fill="#fff"/></svg>
        <span>+ 94 11 5550142</span>
      </li>
      <li>
        <svg class="contact-icon" viewBox="0 0 24 24" aria-hidden="true"><rect x="7" y="4" width="10" height="18" rx="1.5" fill="none" stroke="#fff" stroke-width="1.6"/><rect x="9" y="7" width="6" height="4" fill="#fff"/><line x1="15" y1="1" x2="15" y2="4" stroke="#fff" stroke-width="1.6"/><path d="M9 14h2v2H9zm4 0h2v2h-2zm-4 3h2v2H9zm4 0h2v2h-2z" fill="#fff"/></svg>
        <span>+ 94 77 5550199</span>
      </li>
      <li>
        <svg class="contact-icon" viewBox="0 0 24 24" aria-hidden="true"><rect x="7" y="4" width="10" height="6" fill="#fff"/><path d="M2 12 h20 v8 H2z" fill="#fff"/><rect x="5" y="10" width="14" height="2" fill="#fff"/></svg>
        <span>+ 94 11 5550177</span>
      </li>
      <li>
        <svg class="contact-icon" viewBox="0 0 24 24" aria-hidden="true"><path d="M2 9 L12 3 L22 9 V20 H2 Z" fill="#fff"/><path d="M2 9 L12 15 L22 9" fill="none" stroke="#9c9c9c" stroke-width="1.4"/></svg>
        <span>hello@corvanecolombo.com</span>
      </li>
      <li>
        <svg class="contact-icon" viewBox="0 0 24 24" aria-hidden="true"><g fill="none" stroke="#fff" stroke-width="1.4"><circle cx="12" cy="12" r="10"/><ellipse cx="12" cy="12" rx="4.5" ry="10"/><line x1="2" y1="12" x2="22" y2="12"/><path d="M4 7h16M4 17h16"/></g></svg>
        <span>www.corvanecolombo.com</span>
      </li>
    </ul>

    <address class="company-address">
      <strong>CORVANE LIMITED</strong>
      18, Lotus Grove Road<br>
      Colombo 00300, Sri Lanka
    </address>
  </section>

  <section class="card card--back" aria-label="Business card back">
    <div class="brand-dot" aria-hidden="true"></div>
    <h2 class="brand-name">Corvane<br>Entertainment</h2>
    <p class="tagline">Highest Winning Percentage In The World</p>
    <p class="web-address">www.corvanecolombo.com</p>
  </section>

</main>
</body>
</html>
```